Quorimo Business Card Design Project

We need a business card design for quorimo.example a company based in Berlin, Germany.

?Quorimo is marketplace that enables people all over the world to monetize and exchange their individual knowledge and language skills through interactive video sessions. User are matched by their interests.

On Quorimo everybody can be student or teacher (seller or buyer).

We would love to see designs that use or main color blue and green. The design should communicate what Quorimo enables - see my notice above.

Looking so forward to your designs
Cheers from Berlin,
Lorenz

Target Market(s)

globally

Industry/Entity Type

Teacher

Requirements
Must have
• Lorenz Hubeck
CEO
Quorimo.example

Quorimo e-Services GmbH
Lindenweg 87
10247 Berlin

Fon: +49 30 418 906 25 17
Mobile: 49 172 54 91 37 6
E-Mail: l.hubeck@quorimo.example
Web: www.quorimo.example

```html
<!DOCTYPE html>
<html lang="en">
<head>
<meta charset="utf-8">
<title>Quorimo – Business Card</title>
<link rel="stylesheet" href="https://fonts.googleapis.com/css2?family=Exo+2:wght@400;600;700&display=swap">
<style>
  :root {
    --brand-blue: #1ba1dd;
    --brand-green: #98c13d;
    --ink-grey: #666767;
    --wordmark-grey: #6b6c6d;
    --card-white: #ffffff;
    --backdrop: #e8e9ea;
    --font-main: "Exo 2", "Trebuchet MS", sans-serif;
  }
  * { box-sizing: border-box; margin: 0; padding: 0; }
  html, body {
    width: 954px;
    height: 1200px;
    overflow: hidden;
    background: var(--backdrop);
    font-family: var(--font-main);
  }
  .sheet {
    position: relative;
    width: 954px;
    height: 1200px;
  }
  .card {
    position: absolute;
    left: 78px;
    width: 798px;
    height: 456px;
    border-radius: 24px;
    overflow: hidden;
    background: var(--card-white);
    box-shadow: 0 3px 10px rgba(0,0,0,0.18);
  }
  .card--front { top: 92px; }
  .card--back  { top: 651px; }
  .card__shapes {
    position: absolute;
    inset: 0;
    width: 100%;
    height: 100%;
  }
  .brand {
    position: absolute;
    left: 0;
    width: 412px;
    top: 54px;
    text-align: center;
  }
  .brand__dot {
    display: block;
    width: 112px;
    height: 112px;
    margin: 0 auto;
    border-radius: 50%;
    background: var(--brand-blue);
  }
  .brand__name {
    display: block;
    margin-top: 38px;
    font-size: 70px;
    line-height: 70px;
    font-weight: 600;
    color: var(--wordmark-grey);
    letter-spacing: 1px;
  }
  .brand__tagline {
    display: block;
    margin-top: 2px;
    font-size: 18px;
    font-weight: 700;
    color: var(--brand-blue);
    letter-spacing: 2.6px;
  }
  .company-address {
    position: absolute;
    left: 0;
    width: 412px;
    top: 362px;
    text-align: center;
    font-size: 19px;
    line-height: 26px;
    color: var(--ink-grey);
    letter-spacing: 0.8px;
    font-style: normal;
  }
  .person {
    position: absolute;
    left: 474px;
    top: 46px;
    color: var(--card-white);
  }
  .person__name {
    font-size: 34px;
    font-weight: 700;
    line-height: 40px;
    letter-spacing: 0.4px;
  }
  .person__role {
    font-size: 16px;
    font-weight: 400;
    margin-top: 4px;
  }
  .contact-list {
    position: absolute;
    left: 479px;
    top: 306px;
    list-style: none;
    color: var(--card-white);
    font-size: 20px;
    line-height: 27px;
    letter-spacing: 0.8px;
  }
  .contact-list__item {
    display: flex;
    align-items: center;
    gap: 9px;
  }
  .contact-list__icon {
    width: 18px;
    height: 18px;
    flex: none;
  }
  .web-address {
    position: absolute;
    left: 482px;
    top: 318px;
    font-size: 25px;
    letter-spacing: 0.8px;
    color: var(--card-white);
  }
</style>
</head>
<body>
<main class="sheet">

  <section class="card card--front" aria-label="Business card front">
    <svg class="card__shapes" viewBox="0 0 700 400" preserveAspectRatio="none" aria-hidden="true">
      <path fill="var(--brand-green)" d="M330,97 C350,170 370,240 370,300 C370,340 355,375 340,400 L700,400 L700,97 Z"/>
      <path fill="var(--brand-blue)" stroke="var(--card-white)" stroke-width="3" d="M363,-2 C336,50 326,120 345,190 C360,245 382,290 375,330 C370,360 360,380 352,402 L702,402 L702,-2 Z"/>
    </svg>

    <div class="brand">
      <span class="brand__dot"></span>
      <span class="brand__name">quorimo</span>
      <span class="brand__tagline">share what you know</span>
    </div>

    <address class="company-address">
      Quorimo e-Services GmbH,<br>
      Lindenweg 87, 10247 Berlin
    </address>

    <div class="person">
      <h1 class="person__name">Lorenz Hubeck</h1>
      <p class="person__role">CEO</p>
    </div>

    <ul class="contact-list">
      <li class="contact-list__item">
        <svg class="contact-list__icon" viewBox="0 0 20 20" aria-hidden="true">
          <path fill="#fff" d="M2,7 C2,4 6,3 10,3 C14,3 18,4 18,7 L15,8 L14,6 L6,6 L5,8 Z M5,9 L15,9 L17,16 L3,16 Z"/>
          <circle cx="10" cy="12.5" r="2" fill="var(--brand-blue)"/>
        </svg>
        <span>+49 30 418 906 25 17</span>
      </li>
      <li class="contact-list__item">
        <svg class="contact-list__icon" viewBox="0 0 20 20" aria-hidden="true">
          <rect x="5" y="3" width="10" height="16" rx="2" fill="#fff"/>
          <rect x="7" y="5" width="6" height="5" fill="var(--brand-blue)"/>
          <rect x="12" y="0" width="1.5" height="4" fill="#fff"/>
        </svg>
        <span>49 172 54 91 37 6</span>
      </li>
      <li class="contact-list__item">
        <svg class="contact-list__icon" viewBox="0 0 20 20" aria-hidden="true">
          <rect x="2" y="5" width="16" height="11" rx="1.5" fill="none" stroke="#fff" stroke-width="1.8"/>
          <path d="M2.5,6 L10,12 L17.5,6" fill="none" stroke="#fff" stroke-width="1.8"/>
        </svg>
        <span>l.hubeck@quorimo.example</span>
      </li>
      <li class="contact-list__item">
        <svg class="contact-list__icon" viewBox="0 0 20 20" aria-hidden="true">
          <circle cx="10" cy="10" r="8" fill="#fff"/>
          <path d="M5,6 C7,5 9,7 8,9 C7,11 9,12 8,15 M12,4 C13,7 15,8 16,9 M12,12 C14,12 15,14 14,16" fill="none" stroke="var(--brand-blue)" stroke-width="1.4"/>
        </svg>
        <span>www.quorimo.example</span>
      </li>
    </ul>
  </section>

  <section class="card card--back" aria-label="Business card back">
    <svg class="card__shapes" viewBox="0 0 700 400" preserveAspectRatio="none" aria-hidden="true">
      <path fill="var(--brand-blue)" d="M330,97 C350,170 370,240 370,300 C370,340 355,375 340,400 L700,400 L700,97 Z"/>
      <path fill="var(--brand-green)" stroke="var(--card-white)" stroke-width="3" d="M363,-2 C336,50 326,120 345,190 C360,245 382,290 375,330 C370,360 360,380 352,402 L702,402 L702,-2 Z"/>
    </svg>

    <div class="brand">
      <span class="brand__dot"></span>
      <span class="brand__name">quorimo</span>
      <span class="brand__tagline">share what you know</span>
    </div>

    <p class="web-address">www.quorimo.example</p>
  </section>

</main>
</body>
</html>
```